New Interrior Decoration company needs new website

We need a website for our new company specialising in interior decoration to residential and commercial markets.
We supply and install decorative and printed films for office and home decoration such as feature walls.
We would like to keep the design simple and clean.

Target Market(s)

Architects and interior designaers

Industry/Entity Type

It Company

Number of Pages Required

5+ page

Font styles to use
Sans Serif

Requirements
Must have
• Home page,
• Services/products page (split into commercial and residential)
• Gallery (split into commercial and residential)
• contact form and page
Nice to have
• Very clean and minimalistic design.

```html
<!DOCTYPE html>
<html lang="en">
<head>
<meta charset="utf-8">
<title>Linea Interiors</title>
<link rel="stylesheet" href="https://fonts.googleapis.com/css2?family=Jura:wght@400;500;600&family=Open+Sans:wght@400;600;700&display=swap">
<style>
  :root{
    --blue:#0a5bbf;
    --ink:#2b2b2b;
    --text:#5a5a5a;
    --band:#efefef;
    --white:#ffffff;
    --rule:#d6d6d6;
    --head:"Jura", sans-serif;
    --body:"Open Sans", sans-serif;
  }
  *{box-sizing:border-box;margin:0;padding:0}
  h1,h2,h3{font-weight:400}
  html,body{width:1200px;height:2335px;overflow:hidden;background:var(--white)}
  body{position:relative;font-family:var(--body);color:var(--text)}

  /* header */
  .site-header{position:absolute;left:0;top:0;width:1200px;height:132px;border-top:5px solid var(--blue);background:var(--white)}
  .brand{position:absolute;left:78px;top:30px;display:flex;align-items:center;gap:14px}
  .brand-mark{width:60px;height:60px;background:var(--blue);border-radius:4px}
  .brand-name{font-family:var(--head);font-weight:600;font-size:33px;line-height:1;color:var(--ink);letter-spacing:.5px}
  .top-email{position:absolute;left:622px;top:14px;font-size:15px;color:#333;display:flex;align-items:center;gap:7px}
  .top-phone{position:absolute;left:877px;top:0;width:245px;height:50px;background:var(--blue);border-radius:0 0 6px 6px;color:var(--white);font-family:var(--head);font-weight:600;font-size:25px;display:flex;align-items:center;justify-content:center;gap:8px}
  .nav-link{position:absolute;top:65px;height:47px;line-height:47px;font-family:var(--head);font-weight:500;font-size:22px;color:var(--ink);text-decoration:none;white-space:nowrap}
  .nav-link.active{background:var(--blue);color:var(--white);width:102px;text-align:center}

  /* hero */
  .hero{position:absolute;left:0;top:132px;width:1200px;height:574px;background:linear-gradient(180deg,#6b3348 0%,#7a4150 45%,#c9b9a6 62%,#e7e0d6 80%,#d8d2ca 100%)}
  .hero-arrow{position:absolute;top:238px;width:62px;height:62px;background:var(--blue);border-radius:3px;display:flex;align-items:center;justify-content:center}

  /* welcome */
  .welcome-kicker{position:absolute;left:80px;top:778px;font-family:var(--head);font-size:34px;color:var(--ink)}
  .welcome-title{position:absolute;left:80px;top:822px;font-family:var(--head);font-size:44px;color:var(--blue)}
  .welcome-text{position:absolute;left:80px;top:880px;width:600px;font-size:15px;line-height:25px}
  .btn{position:absolute;background:var(--blue);color:var(--white);font-family:var(--head);font-weight:500;font-size:19px;border-radius:3px;display:flex;align-items:center;justify-content:center}
  .welcome-badge{position:absolute;left:737px;top:787px;width:385px;height:246px;background:var(--blue);border-radius:10px;display:flex;align-items:center;justify-content:center;font-family:var(--head);font-weight:600;font-size:48px;color:var(--white)}

  /* services */
  .services{position:absolute;left:0;top:1115px;width:1200px;height:561px;background:var(--band)}
  .section-title{position:absolute;left:0;width:1200px;text-align:center;font-family:var(--head);font-size:44px;color:var(--ink)}
  .section-title span{color:var(--blue)}
  .services-intro{position:absolute;left:180px;top:116px;width:840px;text-align:center;font-size:15px;line-height:25px}
  .service-card{position:absolute;top:194px;width:313px;text-align:center}
  .service-photo{width:313px;height:156px}
  .service-name{font-family:var(--head);font-weight:500;font-size:26px;color:var(--ink);margin-top:14px}
  .service-text{font-size:15px;line-height:25px;margin:8px 8px 0}
  .service-link{font-family:var(--head);font-weight:500;font-size:19px;color:var(--blue);margin-top:4px}
  .services-divider{position:absolute;left:600px;top:190px;width:1px;height:245px;background:var(--rule)}

  /* gallery */
  .gallery-tile{position:absolute;top:1801px;width:234px;height:156px}

  /* footer */
  .site-footer{position:absolute;left:0;top:2100px;width:1200px;height:235px;background:var(--blue);color:var(--white)}
  .footer-nav{position:absolute;left:80px;top:36px;display:flex;gap:33px;font-family:var(--head);font-weight:500;font-size:19px}
  .social{position:absolute;top:27px;width:46px;height:46px;border:1.5px solid var(--white);border-radius:3px;display:flex;align-items:center;justify-content:center}
  .social::after{content:"";width:14px;height:14px;border-radius:50%;background:var(--white)}
  .social.solid{background:var(--white)}
  .social.solid::after{background:var(--blue)}
  .footer-rule{position:absolute;left:78px;top:101px;width:1044px;height:1px;background:rgba(255,255,255,.25)}
  .footer-heading{position:absolute;left:80px;top:120px;font-family:var(--head);font-weight:500;font-size:20px}
  .contact-item{position:absolute;top:154px;display:flex;align-items:center;gap:12px;font-size:14px;line-height:24px}
  .contact-icon{width:40px;height:40px;background:var(--white);border-radius:4px;display:flex;align-items:center;justify-content:center;flex:none}
  .copyright{position:absolute;left:889px;top:150px;font-size:14px;line-height:25px}
</style>
</head>
<body>

<header class="site-header">
  <div class="brand"><div class="brand-mark"></div><div class="brand-name">LINEA INTERIORS</div></div>
  <div class="top-email">
    <svg width="16" height="12" viewBox="0 0 16 12" fill="none" stroke="#0a5bbf" stroke-width="1.6"><rect x="1" y="1" width="14" height="10" rx="1"/><path d="M1 1l7 6 7-6"/></svg>
    info@lineainteriors.com
  </div>
  <div class="top-phone">
    <svg width="22" height="22" viewBox="0 0 24 24" fill="#fff"><path d="M6.6 10.8a15 15 0 006.6 6.6l2.2-2.2a1 1 0 011-.25 11.4 11.4 0 003.6.6 1 1 0 011 1V20a1 1 0 01-1 1A17 17 0 013 4a1 1 0 011-1h3.5a1 1 0 011 1 11.4 11.4 0 00.6 3.6 1 1 0 01-.25 1z"/></svg>
    123 456 7890
  </div>
  <nav class="main-nav">
    <a class="nav-link active" href="#" style="left:489px">HOME</a>
    <a class="nav-link" href="#" style="left:616px">ABOUT</a>
    <a class="nav-link" href="#" style="left:733px">SERVICES</a>
    <a class="nav-link" href="#" style="left:882px">GALLERY</a>
    <a class="nav-link" href="#" style="left:1024px">CONTACT</a>
  </nav>
</header>

<section class="hero" role="img" aria-label="Living room with a cream sectional sofa, black cushions, low coffee table with a flower vase and a textured plum feature wall">
  <div class="hero-arrow" style="left:78px"><svg width="16" height="30" viewBox="0 0 16 30" fill="none" stroke="#fff" stroke-width="2"><path d="M13 2L3 15l10 13"/></svg></div>
  <div class="hero-arrow" style="left:1060px"><svg width="16" height="30" viewBox="0 0 16 30" fill="none" stroke="#fff" stroke-width="2"><path d="M3 2l10 13L3 28"/></svg></div>
</section>

<section class="welcome">
  <h2 class="welcome-kicker">WELCOME TO</h2>
  <h1 class="welcome-title">LINEA INTERIORS</h1>
  <p class="welcome-text">Lorem Ipsum is simply dummy text of the printing and typesetting industry. Lorem Ipsum has been the industry's standard dummy text ever since the 1500s, when an unknown printer took a galley of type and scrambled it to make a type specimen book.</p>
  <div class="btn" style="left:78px;top:995px;width:166px;height:52px">READ MORE</div>
  <div class="welcome-badge">LINEA</div>
</section>

<section class="services">
  <h2 class="section-title" style="top:50px">SERVICES <span>WE PROVIDE</span></h2>
  <p class="services-intro">Lorem Ipsum is simply dummy text of the printing and typesetting industry. Lorem Ipsum has been the industry's standard dummy text ever since the 1500.</p>
  <article class="service-card" style="left:228px">
    <div class="service-photo" role="img" aria-label="Grey residential kitchen with pendant lamps and open shelving" style="background:linear-gradient(180deg,#8d9092,#b9bcbc 60%,#6f7274)"></div>
    <h3 class="service-name">Residential Interiors</h3>
    <p class="service-text">Lorem Ipsum is simply dummy text of the printing and typesetting industry. Lorem Ipsum has been the industry.</p>
    <div class="service-link">READ MORE &raquo;</div>
  </article>
  <div class="services-divider"></div>
  <article class="service-card" style="left:667px">
    <div class="service-photo" role="img" aria-label="Bright commercial office with a curved wooden reception desk" style="background:linear-gradient(180deg,#cfccc4,#e6e1d6 55%,#b99a6d)"></div>
    <h3 class="service-name">Commercial Interiors</h3>
    <p class="service-text">Lorem Ipsum is simply dummy text of the printing and typesetting industry. Lorem Ipsum has been the industry.</p>
    <div class="service-link">READ MORE &raquo;</div>
  </article>
</section>

<section class="gallery">
  <h2 class="section-title" style="top:1726px">LATEST <span>GALLERY</span></h2>
  <div class="gallery-tile" style="left:78px;background:linear-gradient(135deg,#2a241e,#6d5a45 50%,#1c1814)" role="img" aria-label="Dim lounge with a textured stone feature wall and dark vases"></div>
  <div class="gallery-tile" style="left:348px;background:linear-gradient(135deg,#4a1d12,#8a3a22 50%,#2a1c20)" role="img" aria-label="Rust red feature wall with a white lounge chair and bookshelf"></div>
  <div class="gallery-tile" style="left:619px;background:linear-gradient(135deg,#9da39c,#c6c8bf 50%,#5c6a66)" role="img" aria-label="Hallway with a grey stone effect wall"></div>
  <div class="gallery-tile" style="left:889px;background:linear-gradient(135deg,#8a3b2a,#b0604a 50%,#d6d2c8)" role="img" aria-label="Red brick effect wall with a dark sofa and white shelving"></div>
  <div class="btn" style="left:525px;top:1992px;width:150px;height:51px">VIEW ALL</div>
</section>

<footer class="site-footer">
  <nav class="footer-nav"><span>Home</span><span>About</span><span>Services</span><span>Gallery</span><span>Contact</span></nav>
  <div class="social solid" style="left:855px" aria-label="Social link"></div>
  <div class="social" style="left:928px" aria-label="Social link"></div>
  <div class="social" style="left:1001px" aria-label="Social link"></div>
  <div class="social" style="left:1075px" aria-label="Social link"></div>
  <div class="footer-rule"></div>
  <div class="footer-heading">Contact Us</div>
  <div class="contact-item" style="left:78px">
    <div class="contact-icon"><svg width="14" height="20" viewBox="0 0 14 20" fill="#2b2b2b"><path d="M7 0a7 7 0 00-7 7c0 5 7 13 7 13s7-8 7-13a7 7 0 00-7-7zm0 9.5A2.5 2.5 0 117 4.5a2.5 2.5 0 010 5z"/></svg></div>
    <span>Lorem Ipsum is dummy<br>text of the printing.</span>
  </div>
  <div class="contact-item" style="left:348px">
    <div class="contact-icon"><svg width="18" height="18" viewBox="0 0 24 24" fill="#2b2b2b"><path d="M6.6 10.8a15 15 0 006.6 6.6l2.2-2.2a1 1 0 011-.25 11.4 11.4 0 003.6.6 1 1 0 011 1V20a1 1 0 01-1 1A17 17 0 013 4a1 1 0 011-1h3.5a1 1 0 011 1 11.4 11.4 0 00.6 3.6 1 1 0 01-.25 1z"/></svg></div>
    <strong>123 456 7890</strong>
  </div>
  <div class="contact-item" style="left:602px">
    <div class="contact-icon"><svg width="18" height="14" viewBox="0 0 16 12" fill="none" stroke="#2b2b2b" stroke-width="1.6"><rect x="1" y="1" width="14" height="10" rx="1"/><path d="M1 1l7 6 7-6"/></svg></div>
    <span>info@lineainteriors.com</span>
  </div>
  <p class="copyright">&copy; <strong>LINEA INTERIORS</strong> - 2016.<br>All Rights Reserved.</p>
</footer>

</body>
</html>
```